Business Card Design Project

Business card based on attached logo

Todd Merrick
Todd@lorvantest.com
877-514-9073 ext. 318
Www.LorvanTest.com

Industry/Entity Type

Business

```html
<!DOCTYPE html>
<html lang="en">
<head>
<meta charset="utf-8">
<title>LorvanTest Business Card</title>
<link rel="stylesheet" href="https://fonts.googleapis.com/css2?family=Roboto:wght@400;700;900&display=swap">
<style>
  :root {
    --stage: #e9e6e2;
    --card-white: #ffffff;
    --card-grey-top: #f4f4f4;
    --card-grey-bottom: #e2e2e2;
    --brand-red: #e31c24;
    --brand-red-deep: #a8171d;
    --ink: #111111;
    --ink-soft: #333333;
    --label: #2a2a2a;
  }
  * { box-sizing: border-box; margin: 0; padding: 0; }
  html, body { width: 1200px; height: 788px; overflow: hidden; }
  body {
    background: var(--stage);
    font-family: "Roboto", Arial, sans-serif;
    position: relative;
  }
  .side-label {
    position: absolute;
    width: 527px;
    text-align: center;
    font-size: 20px;
    color: var(--label);
  }
  .card {
    position: absolute;
    width: 527px;
    height: 301px;
    border-radius: 22px;
    overflow: hidden;
    background: var(--card-white);
    box-shadow: 0 4px 10px rgba(0,0,0,.25);
  }
  .card--front { left: 53px; top: 73px; }
  .card--back-white { left: 621px; top: 73px; }
  .card--back-red {
    left: 53px; top: 444px;
    background: linear-gradient(180deg, var(--brand-red) 0%, var(--brand-red-deep) 100%);
  }
  .card--back-grey {
    left: 621px; top: 444px;
    background: linear-gradient(180deg, var(--card-grey-top) 0%, var(--card-grey-bottom) 100%);
  }
  .front-band {
    position: absolute;
    left: 0; right: 0; bottom: 0;
    height: 54px;
    background: linear-gradient(180deg, var(--brand-red) 0%, var(--brand-red-deep) 100%);
  }
  .wordmark {
    position: absolute;
    display: flex;
    align-items: center;
    gap: 10px;
    font-weight: 900;
    color: var(--ink);
    letter-spacing: -1px;
    line-height: 1;
  }
  .wordmark__square { background: var(--brand-red); flex: none; }
  .card--front .wordmark { left: 36px; top: 62px; font-size: 50px; }
  .card--front .wordmark__square { width: 22px; height: 22px; }
  .card--back-white .wordmark,
  .card--back-red .wordmark { left: 0; right: 0; justify-content: center; top: 100px; font-size: 54px; }
  .card--back-white .wordmark__square,
  .card--back-red .wordmark__square { width: 24px; height: 24px; }
  .card--back-red .wordmark__square { background: var(--card-white); }
  .card--back-grey .wordmark { left: 0; right: 0; justify-content: center; top: 46px; font-size: 38px; }
  .card--back-grey .wordmark__square { width: 18px; height: 18px; }
  .contact-name {
    position: absolute; left: 50px; top: 202px;
    font-size: 17px; font-weight: 700; color: var(--brand-red);
  }
  .contact-phone {
    position: absolute; left: 50px; top: 232px;
    font-size: 12.5px; color: var(--ink-soft);
  }
  .contact-phone b, .contact-web b { font-weight: 700; }
  .contact-web {
    position: absolute; right: 13px; top: 253px;
    text-align: right; font-size: 12.5px; line-height: 19px; color: var(--card-white);
  }
  .site-url {
    position: absolute; left: 0; right: 0; top: 250px;
    text-align: center; font-size: 18px; color: var(--ink-soft);
  }
  .card--back-red .site-url { color: var(--card-white); }
  .plaque {
    position: absolute; left: 82px; top: 83px;
    width: 360px; height: 128px;
    background: var(--card-white);
    border: 1px solid #dcdcdc;
    box-shadow: 0 6px 8px rgba(0,0,0,.18);
  }
</style>
</head>
<body>
  <div class="side-label" style="left:53px; top:34px;">Front</div>
  <div class="side-label" style="left:621px; top:34px;">Back - 1</div>
  <div class="side-label" style="left:53px; top:405px;">Back - 2</div>
  <div class="side-label" style="left:621px; top:405px;">Back - 3</div>

  <section class="card card--front">
    <div class="front-band" role="img" aria-label="Decorative red and black curved band across the lower card"></div>
    <div class="wordmark"><span>LorvanTest</span><span class="wordmark__square"></span></div>
    <p class="contact-name">Todd Merrick</p>
    <p class="contact-phone"><b>p :</b> 877-514-9073 ext. 318</p>
    <p class="contact-web"><b>e :</b> Todd@lorvantest.com<br><b>w :</b> www.LorvanTest.com</p>
  </section>

  <section class="card card--back-white">
    <div class="wordmark"><span>LorvanTest</span><span class="wordmark__square"></span></div>
    <p class="site-url">www.LorvanTest.com</p>
  </section>

  <section class="card card--back-red">
    <div class="wordmark"><span>LorvanTest</span><span class="wordmark__square"></span></div>
    <p class="site-url">www.LorvanTest.com</p>
  </section>

  <section class="card card--back-grey">
    <div class="plaque">
      <div class="wordmark"><span>LorvanTest</span><span class="wordmark__square"></span></div>
    </div>
    <p class="site-url">www.LorvanTest.com</p>
  </section>
</body>
</html>
```